Webdesign für Heilpraktiker
Zielgruppe
Ich bin Heilpraktiker und betreibe eine Naturheilpraxis mit den Schwerpunkten der traditionellen chinesischen Medizin (TCM). Da ganz besonders in der Philosophie (sogenannte 'Schule' des Wo Shen). Aber auch in der traditionellen Heilweise der TCM, wie Akupunktur, Heilkräutermedizin und weiteres.
Die Zielgruppe sind Menschen, die medizinische Hilfe benötigen. (Vom Kind bis zum älteren Menschen).
Aufgabenstellung
Es gibt ein Praxislogo, ein Foto von mir und ggf. ein Landschaftsbild. Ich dachte an fünf Hauptseiten mit Untergruppen. Am Ende sollte alles in Wordpress formatiert werden können, um es zu veröffentlichen.
Weitere Fotos zur Unterstützung der Themen kann ich natürlich gerne liefern.
Die Gestaltung ist nicht festgesetzt. Sollte aber seriös rüber kommen.

```html
<!DOCTYPE html>
<html lang="de">
<head>
<meta charset="utf-8">
<title>Naturheilpraxis Konrad Fellnroth</title>
<link rel="stylesheet" href="https://fonts.googleapis.com/css2?family=Lato:wght@300;400;700;900&display=swap">
<style>
:root{
  --gold:#dcae6a;
  --dark:#232323;
  --footer:#3d3d3d;
  --text:#2f2f2f;
  --muted:#a9a9a9;
  --line:#d9d9d9;
  --white:#ffffff;
}
*{margin:0;padding:0;box-sizing:border-box}
html,body{width:716px;height:1200px;overflow:hidden}
body{position:relative;font-family:'Lato',sans-serif;color:var(--text);background:var(--white)}
.abs{position:absolute}
.topnav{left:0;top:0;width:716px;height:23px;background:var(--dark);display:flex;padding-left:107px}
.topnav a{color:var(--white);font-size:7px;font-weight:700;text-decoration:none;line-height:23px;padding:0 10px;white-space:nowrap}
.topnav a.active{background:var(--gold);color:var(--dark);width:60px;text-align:center;padding:0}
.hero{left:0;top:23px;width:716px;height:302px;background:linear-gradient(180deg,#8f9ea8 0%,#a7b08c 22%,#7f9a3d 45%,#93ac3f 65%,#6f8a2f 100%)}
.hero svg{position:absolute;left:0;top:0}
.hero-title{left:0;top:150px;width:716px;text-align:center;color:var(--white);font-size:24px;line-height:29px;font-weight:400}
.hero-title b{font-weight:900}
.hero-title .light{font-weight:300}
.brand{left:325px;top:27px;width:66px;height:66px;border-radius:50%;background:var(--white);border:1px solid var(--dark);display:flex;align-items:center;justify-content:center;text-align:center;font-size:7px;font-weight:700;color:var(--dark);line-height:9px}
.portrait-frame{left:90px;top:356px;width:169px;height:182px;border:1px solid var(--line);background:var(--white);box-shadow:0 7px 6px -6px rgba(0,0,0,.35)}
.portrait{position:absolute;left:8px;top:8px;width:152px;height:164px;background:linear-gradient(160deg,#c8c8c8,#7d7d7d 60%,#3a3a3a)}
.profile-name{left:298px;top:367px;font-size:13px;letter-spacing:1.6px;font-weight:700;color:var(--gold)}
.profile-sub{left:298px;top:386px;width:300px;font-size:7.5px;line-height:9px}
.facts{left:300px;top:424px;list-style:none}
.facts li{display:flex;align-items:center;height:18px;font-size:8px}
.facts svg{margin-right:9px}
.panels{left:0;top:564px;width:716px;height:224px;border-top:1px solid var(--line);border-bottom:1px solid var(--line)}
.panels .divider{position:absolute;left:358px;top:0;width:1px;height:224px;background:var(--line)}
.panel-heading{font-size:9px;font-weight:700;letter-spacing:1.2px;color:var(--gold)}
.copy{font-size:7.5px;line-height:11.6px}
.copy p{margin-bottom:4.3px}
.help-intro{left:89px;top:865px;width:260px;font-size:7.5px;line-height:11.6px;font-weight:700}
.help-list{left:90px;top:901px;width:265px;list-style:none}
.help-list li{display:flex;font-size:7.5px;line-height:11.6px;margin-bottom:6.4px}
.help-list svg{flex:none;margin:2px 9px 0 0}
.more-btn{left:90px;top:1048px;width:76px;height:23px;background:var(--gold);color:var(--dark);font-size:7.5px;display:flex;align-items:center;justify-content:center;gap:5px}
.quick-contact{left:387px;top:833px;width:239px;height:245px;background:var(--gold);border-radius:4px}
.quick-contact h2{position:absolute;top:14px;width:100%;text-align:center;font-size:13px;font-weight:700;color:var(--text)}
.field{position:absolute;left:22px;width:196px;height:21px;background:var(--white);border-radius:2px;font-size:6.5px;color:#8a8a8a;padding:6px 10px}
.send{position:absolute;left:21px;top:201px;width:197px;height:26px;background:var(--footer);border-radius:2px;color:var(--white);font-size:8.5px;font-weight:700;letter-spacing:.6px;display:flex;align-items:center;justify-content:center;gap:8px}
.footer{left:0;top:1115px;width:716px;height:85px;background:var(--footer);color:var(--muted);font-size:7px;line-height:10.6px}
.footer .brand-small{position:absolute;left:92px;top:22px;width:47px;height:47px;border-radius:50%;border:1px solid #d8d8d8;display:flex;align-items:center;justify-content:center;font-size:5.5px;font-weight:700;color:#d8d8d8;text-align:center;line-height:7px}
.footer .col{position:absolute;top:25px}
.footer .row{display:flex;gap:7px;align-items:flex-start;margin-bottom:5px}
</style>
</head>
<body>

<nav class="topnav abs">
  <a class="active">STARTSEITE</a>
  <a>ZU MEINER PERSON</a>
  <a>WOBEI KANN ICH HELFEN</a>
  <a>DER ERSTE BESUCH</a>
  <a>WAS IST DAS WO SHEN</a>
  <a>KONTACT</a>
</nav>

<section class="hero abs" role="img" aria-label="Landschaftsfoto: grüne Hügel und Berge unter bewölktem Himmel">
  <svg width="716" height="302" viewBox="0 0 716 302">
    <path d="M0 0H716V26C520 48 300 58 0 38Z" fill="#dcae6a"/>
    <path d="M0 0H716V22C520 42 300 52 0 33Z" fill="#ffffff"/>
    <path d="M0 302V296C220 270 470 268 716 282V302Z" fill="#dcae6a"/>
    <path d="M0 302V300C220 276 470 274 716 288V302Z" fill="#ffffff"/>
  </svg>
</section>
<div class="hero-title abs"><b>Naturheilpraxis</b> <span class="light">des</span><br>Heilpraktiker Konrad Fellnroth</div>
<div class="brand abs">Praxis<br>Fellnroth</div>

<div class="portrait-frame abs">
  <div class="portrait" role="img" aria-label="Porträtfoto des Heilpraktikers"></div>
</div>
<div class="profile-name abs">KONRAD FELLNROTH</div>
<div class="profile-sub abs">Heilpraktiker und zertifizierter Therapeut der traditionellen chinesischen Medizin (Berufsverband VTH e.V.)</div>
<ul class="facts abs">
  <li><svg width="13" height="13" viewBox="0 0 13 13"><path d="M11.5 5.5A5.2 5.2 0 1 1 9 2" fill="none" stroke="#2f2f2f" stroke-width="1.1"/><path d="M4 6.5l2.3 2.3L12 2.8" fill="none" stroke="#dcae6a" stroke-width="1.3"/></svg>Jahrgang 1967</li>
  <li><svg width="13" height="13" viewBox="0 0 13 13"><path d="M11.5 5.5A5.2 5.2 0 1 1 9 2" fill="none" stroke="#2f2f2f" stroke-width="1.1"/><path d="M4 6.5l2.3 2.3L12 2.8" fill="none" stroke="#dcae6a" stroke-width="1.3"/></svg>Seit 2006 Heilpraktiker in Braunschweig</li>
  <li><svg width="13" height="13" viewBox="0 0 13 13"><path d="M11.5 5.5A5.2 5.2 0 1 1 9 2" fill="none" stroke="#2f2f2f" stroke-width="1.1"/><path d="M4 6.5l2.3 2.3L12 2.8" fill="none" stroke="#dcae6a" stroke-width="1.3"/></svg>Seit 2010 Gründer und Leiter des MBL Blutanalyselabors in Braunschweig</li>
  <li><svg width="13" height="13" viewBox="0 0 13 13"><path d="M11.5 5.5A5.2 5.2 0 1 1 9 2" fill="none" stroke="#2f2f2f" stroke-width="1.1"/><path d="M4 6.5l2.3 2.3L12 2.8" fill="none" stroke="#dcae6a" stroke-width="1.3"/></svg>Seit 2015 zertifizierter TCM Therapeut (Berufsverband VTH e.V.)</li>
  <li><svg width="13" height="13" viewBox="0 0 13 13"><path d="M11.5 5.5A5.2 5.2 0 1 1 9 2" fill="none" stroke="#2f2f2f" stroke-width="1.1"/><path d="M4 6.5l2.3 2.3L12 2.8" fill="none" stroke="#dcae6a" stroke-width="1.3"/></svg>Beschäftigung mit der Wo Shen Philosophie (Schule) seit 1988</li>
</ul>

<section class="panels abs">
  <div class="divider"></div>
  <svg class="abs" style="left:89px;top:16px" width="34" height="31" viewBox="0 0 34 31">
    <rect x="2" y="3" width="22" height="13" rx="6.5" transform="rotate(-35 13 9.5)" fill="#dcae6a"/>
    <ellipse cx="22" cy="21" rx="10" ry="5" fill="#fff" stroke="#2f2f2f" stroke-width="1.4"/>
    <path d="M13 22q9 2 18-2" fill="none" stroke="#2f2f2f" stroke-width="1.2"/>
  </svg>
  <div class="panel-heading abs" style="left:89px;top:54px">WAS MACHE ICH</div>
  <div class="copy abs" style="left:89px;top:76px;width:240px">
    <p>Seit vielen Jahrzehnten begeistere ich mich für die Themen der Medizin und die Wiederherstellung der Gesundheit.</p>
    <p>Ein grundlegendes Gesundheitssystem habe ich schon immer in der traditionellen chinesischen Medizin gesehen.</p>
    <p>Die traditionelle chinesische Medizin ist eine der ältesten Heilkunde- und Therapieform der Welt. Unzählige Therapierichtungen, sogenannte „Schulen“, sind im Laufe der vergangenen Jahrtausende entstanden.</p>
    <p>Eine dieser Richtungen ist die Schule des „Wo Shen“. Diese besteht aus philosophischen Betrachtungen, Erklärungsformen und konkreten Therapieformen.</p>
  </div>
  <svg class="abs" style="left:393px;top:16px" width="34" height="31" viewBox="0 0 34 31">
    <circle cx="3" cy="3" r="1.6" fill="none" stroke="#2f2f2f"/><circle cx="7" cy="3" r="1.6" fill="none" stroke="#2f2f2f"/><circle cx="6" cy="8" r="1.4" fill="none" stroke="#2f2f2f"/>
    <path d="M2 12h8M3 12v14a2 2 0 0 0 4 0V12" fill="none" stroke="#2f2f2f" stroke-width="1.2"/>
    <path d="M16 28h16M20 20a8 8 0 0 0 8 -14M26 2l4 3-6 9-4-3z" fill="none" stroke="#dcae6a" stroke-width="1.3"/>
  </svg>
  <div class="panel-heading abs" style="left:393px;top:54px">DIE PRAXIS</div>
  <div class="copy abs" style="left:393px;top:76px;width:240px;line-height:13.5px">
    Seit 2012 besteht die Praxis, in der sich auch das MBL Blutanalyselabor befindet, im dritten Stock eines Wohn- und Geschäftshauses in der Braunschweiger Innenstadt. Ein Aufzug ist vorhanden. Die Praxis ist gut mit öffentlichen Verkehrsmitteln zu erreichen und hat in unmittelbarer Nähe auch ein Parkhaus. (Tiefgarage und Haltstelle Packhof)
  </div>
</section>

<svg class="abs" style="left:90px;top:807px" width="32" height="39" viewBox="0 0 32 39">
  <rect x="6" y="1" width="11" height="14" rx="5.5" fill="none" stroke="#dcae6a" stroke-width="1.3"/>
  <path d="M1 30v-7a5 5 0 0 1 5-5h10M1 30h12" fill="none" stroke="#dcae6a" stroke-width="1.3"/>
  <circle cx="23" cy="27" r="6" fill="none" stroke="#2f2f2f" stroke-width="1.5"/>
  <path d="M20 32l-2 6 3-2 2 2M26 32l2 6-3-2-2 2M20.5 27l2 2 3-3.5" fill="none" stroke="#2f2f2f" stroke-width="1.2"/>
</svg>
<div class="panel-heading abs" style="left:90px;top:849px">WOBEI KANN ICH HELFEN</div>
<div class="help-intro abs">Der Schwerpunkt meiner Tätigkeit ist die Beseitigung und Linderung von chronischen Erkrankungen und deren Folgen. Hierzu zählen u.a.:</div>
<ul class="help-list abs">
  <li><svg width="9" height="8" viewBox="0 0 9 8"><path d="M1 4l2.5 2.5L8 1" fill="none" stroke="#dcae6a" stroke-width="1.3"/></svg>Der rheumatische Formenkreis / Erkrankungen die mit Entzündungen und Schmerzzuständen einhergehen</li>
  <li><svg width="9" height="8" viewBox="0 0 9 8"><path d="M1 4l2.5 2.5L8 1" fill="none" stroke="#dcae6a" stroke-width="1.3"/></svg>Magen- und Darmbeschwerden / Unverträglichkeiten bis hin zu allergischen Dispositionen</li>
  <li><svg width="9" height="8" viewBox="0 0 9 8"><path d="M1 4l2.5 2.5L8 1" fill="none" stroke="#dcae6a" stroke-width="1.3"/></svg>Diabetes / Stoffwechselstörungen</li>
  <li><svg width="9" height="8" viewBox="0 0 9 8"><path d="M1 4l2.5 2.5L8 1" fill="none" stroke="#dcae6a" stroke-width="1.3"/></svg>Chronische virale- und bakterielle Belastungen</li>
  <li><svg width="9" height="8" viewBox="0 0 9 8"><path d="M1 4l2.5 2.5L8 1" fill="none" stroke="#dcae6a" stroke-width="1.3"/></svg>Belastungen psychischer Natur / Erschöpfungszustände</li>
  <li><svg width="9" height="8" viewBox="0 0 9 8"><path d="M1 4l2.5 2.5L8 1" fill="none" stroke="#dcae6a" stroke-width="1.3"/></svg>Long Covid Belastungen</li>
</ul>
<div class="more-btn abs"><svg width="8" height="5" viewBox="0 0 8 5"><path d="M0 2.5h7M5 .5l2 2-2 2" fill="none" stroke="#232323" stroke-width=".8"/></svg>Lern mehr</div>

<form class="quick-contact abs">
  <h2>Schneller Kontakt</h2>
  <div class="field" style="top:49px">Vollständiger Name</div>
  <div class="field" style="top:74px">Email</div>
  <div class="field" style="top:100px">Telefon</div>
  <div class="field" style="top:125px;height:71px">Ihre Anfrage</div>
  <div class="send"><svg width="10" height="10" viewBox="0 0 10 10"><path d="M9.5.5L.5 5l3.5 1 1 3.5zM4 6L9.5.5" fill="none" stroke="#fff" stroke-width=".8"/></svg>SENDEN</div>
</form>

<footer class="footer abs">
  <div class="brand-small">Praxis<br>Fellnroth</div>
  <div class="col" style="left:201px">
    <div class="row"><svg width="9" height="11" viewBox="0 0 9 11"><path d="M4.5 10.5S.5 6.5.5 4a4 4 0 0 1 8 0c0 2.5-4 6.5-4 6.5z" fill="#dcae6a"/><circle cx="4.5" cy="4" r="1.5" fill="#3d3d3d"/></svg><div>Konrad Fellnroth<br>Lindenweg 12<br>38100 Braunschweig</div></div>
  </div>
  <div class="col" style="left:357px">
    <div class="row"><svg width="9" height="9" viewBox="0 0 9 9"><path d="M2 .5l1.5 2-1 1.2a5 5 0 0 0 2.8 2.8l1.2-1 2 1.5-1 1.5C4.5 8.5.5 4.5 .5 1.5z" fill="none" stroke="#dcae6a" stroke-width=".8"/></svg><div>Telefon 0531 – 482 17 09</div></div>
    <div class="row"><svg width="10" height="8" viewBox="0 0 10 8"><rect x=".5" y=".5" width="9" height="7" fill="none" stroke="#dcae6a" stroke-width=".8"/><path d="M.5.5L5 4.5 9.5.5" fill="none" stroke="#dcae6a" stroke-width=".8"/></svg><div>Post@heilpraktiker-fellnroth.de</div></div>
  </div>
  <div class="col" style="left:556px;line-height:13.5px">Impressum<br>Datenschutzerklärung</div>
</footer>

</body>
</html>
```